Label for kQm Ranch beef tallow

I need a small label to go on a 2oz amber glass jar as well as a 4 oz. amber glass jar of moisturizer.
I prefer it to be rectangular for the 2oz jar since it's small and square for the 4oz jar.
I'd like to keep our kQm Ranch logo the same font and style, which is attached. Ten Sleep, Wyoming should be left out. The font for kQm Ranch is spartan.
The label content is as follows:
Signature Tallow
Whipped Moisturizer
Ingredients: Beef Tallow, jojoba oil, peppermint oil.
2oz. jar

Instead of a white label, I'm thinking of a tan or brown label that will blend in with the amber jar. The lettering could then be a white, cream or even rust/burgandy color. Something to give it a rich look.

Thank you!

Target Market(s)

Mainly women but men as well.

Industry/Entity Type

Ranching and online beef sales

Requirements
Must have
• kQm Ranch logo

```html
<!DOCTYPE html>
<html lang="en">
<head>
<meta charset="utf-8">
<title>kQm Ranch – Signature Tallow Labels</title>
<link href="https://fonts.googleapis.com/css2?family=Jost:wght@400;500;600&family=League+Spartan:wght@300&display=swap" rel="stylesheet">
<style>
  :root {
    --canvas-bg: #e6e6e6;
    --label-bg: #ffffff;
    --ink: #111111;
    --band: #151515;
    --band-text: #ffffff;
    --art-light: #d9d9d9;
    --art-dark: #3a3a3a;
  }
  * { box-sizing: border-box; margin: 0; padding: 0; }
  html, body { width: 1200px; height: 1200px; overflow: hidden; }
  body {
    background: var(--canvas-bg);
    font-family: "Jost", Arial, sans-serif;
    color: var(--ink);
    position: relative;
  }
  .label {
    position: absolute;
    background: var(--label-bg);
    overflow: hidden;
  }
  .label--2oz { left: 62px; top: 470px; width: 504px; height: 273px; border-radius: 30px; }
  .label--4oz { left: 634px; top: 350px; width: 503px; height: 500px; border-radius: 36px; }

  .product-line {
    position: absolute;
    font-weight: 400;
    letter-spacing: 0.01em;
    white-space: nowrap;
  }
  .label--2oz .product-line { left: 28px; top: 18px; font-size: 20px; }
  .label--4oz .product-line { left: 0; right: 0; top: 42px; text-align: center; font-size: 33px; }

  .brand-name {
    position: absolute;
    font-family: "League Spartan", "Jost", sans-serif;
    font-weight: 300;
    color: var(--ink);
    white-space: nowrap;
    line-height: 1;
  }
  .label--2oz .brand-name { left: 160px; top: 110px; font-size: 44px; }
  .label--4oz .brand-name { left: 40px; top: 220px; font-size: 62px; }

  .cow-art {
    position: absolute;
    background: linear-gradient(180deg, var(--art-light), var(--art-dark) 55%, var(--art-light));
    border-radius: 10px;
    opacity: 0.85;
  }
  .label--2oz .cow-art { left: 398px; top: 22px; width: 92px; height: 186px; }
  .label--4oz .cow-art { left: 378px; top: 140px; width: 112px; height: 220px; }

  .ingredients {
    position: absolute;
    font-weight: 600;
  }
  .label--2oz .ingredients { left: 34px; top: 118px; font-size: 14px; line-height: 1.25; }
  .label--4oz .ingredients { left: 0; right: 0; top: 428px; text-align: center; font-size: 19px; }

  .variant-band {
    position: absolute;
    left: 0; right: 0;
    background: var(--band);
    color: var(--band-text);
    text-align: center;
    font-weight: 500;
    letter-spacing: 0.01em;
  }
  .label--2oz .variant-band { top: 210px; height: 30px; line-height: 30px; font-size: 22px; }
  .label--4oz .variant-band { top: 370px; height: 44px; line-height: 44px; font-size: 33px; }

  .net-weight {
    position: absolute;
    left: 0; right: 0;
    text-align: center;
    font-weight: 600;
  }
  .label--2oz .net-weight { top: 246px; font-size: 13px; }
  .label--4oz .net-weight { top: 468px; font-size: 16px; }
</style>
</head>
<body>
  <section class="label label--2oz">
    <p class="product-line">SIGNATURE TALLOW</p>
    <p class="ingredients">Ingredients:<br>Beef Tallow,<br>jojoba oil,<br>peppermint oil</p>
    <p class="brand-name">kQm Ranch</p>
    <div class="cow-art" role="img" aria-label="Black and white line illustration of a standing dairy cow"></div>
    <p class="variant-band">WHIPPED MOISTURIZER</p>
    <p class="net-weight">2oz.</p>
  </section>

  <section class="label label--4oz">
    <p class="product-line">SIGNATURE TALLOW</p>
    <p class="brand-name">kQm Ranch</p>
    <div class="cow-art" role="img" aria-label="Black and white line illustration of a standing dairy cow"></div>
    <p class="variant-band">WHIPPED MOISTURIZER</p>
    <p class="ingredients">Beef Tallow, jojoba oil, peppermint oil</p>
    <p class="net-weight">4oz.</p>
  </section>
</body>
</html>
```